Signage Design Project

Busisness is a bakery and deli long time owned by the Tavel family. Want to develop a new outside sign that communicates it is a deli and a bakery but keeps the tavel name in the design.

The sign when produced will be about 10' by 3' . It is not lighted at present but could be if it were advantageous.

The name of the store is:

Tavel's Harbor Lane Bakery and Deli. The concept is to have a new,modern sign that reinforces that it is a deli and a bakery, as most people only know about the bakery side of the business
Updates

The name Tavel is just a reinforcer so the people kno it is still in the family.  The emphasis should be on the HARBOR LANE BAKERY and DELI

Target Market(s)

Small business breakfast and lunch customers

Industry/Entity Type

Bakery

Requirements
Must have
• Great impact from the road. Communicate that it is a deli and a bakery. Keep the Tavel name but need not be a major design element

```html
<!DOCTYPE html>
<html lang="en">
<head>
<meta charset="utf-8">
<title>Tavel's Harbor Lane Bakery and Deli – Sign</title>
<link rel="stylesheet" href="https://fonts.googleapis.com/css2?family=Righteous&display=swap">
<style>
  :root {
    --sign-yellow: #ffd200;
    --sign-glow: #fff7a8;
    --sign-border: #3a3000;
    --wordmark-orange: #ee7f1c;
    --ornament-tone: #ffe680;
  }
  html, body {
    margin: 0;
    padding: 0;
    width: 1200px;
    height: 360px;
    overflow: hidden;
    background: #ffffff;
  }
  .sign {
    position: relative;
    width: 1200px;
    height: 360px;
    box-sizing: border-box;
    border: 1px solid var(--sign-border);
    background: radial-gradient(ellipse 42% 75% at 50% 45%, var(--sign-glow) 0%, #fff27a 45%, var(--sign-yellow) 100%);
    overflow: hidden;
  }
  .sign__ornament {
    position: absolute;
    top: 14px;
    width: 62px;
    height: 330px;
    border-radius: 30px;
    background: linear-gradient(180deg, var(--ornament-tone), #ffdc3a 50%, var(--ornament-tone));
    opacity: 0.75;
  }
  .sign__ornament--left { left: 12px; }
  .sign__ornament--right { right: 12px; }
  .wordmark {
    position: absolute;
    inset: 0;
    margin: 0;
    font-family: "Righteous", sans-serif;
    font-weight: 400;
    font-style: normal;
    color: var(--wordmark-orange);
    line-height: 1;
  }
  .wordmark__top {
    position: absolute;
    left: 170px;
    top: 72px;
    width: 850px;
    display: flex;
    align-items: baseline;
    gap: 26px;
  }
  .wordmark__family {
    font-size: 50px;
  }
  .wordmark__place {
    font-size: 84px;
    letter-spacing: 2px;
  }
  .wordmark__trade {
    position: absolute;
    left: 0;
    right: 0;
    top: 182px;
    text-align: center;
    font-size: 124px;
    letter-spacing: 2px;
  }
</style>
</head>
<body>
  <div class="sign">
    <div class="sign__ornament sign__ornament--left" role="img" aria-label="Cream scroll ornament running down the left edge"></div>
    <div class="sign__ornament sign__ornament--right" role="img" aria-label="Cream scroll ornament running down the right edge"></div>
    <h1 class="wordmark">
      <span class="wordmark__top">
        <span class="wordmark__family">Tavel's</span>
        <span class="wordmark__place">HARBOR LANE</span>
      </span>
      <span class="wordmark__trade">Bakery and Deli</span>
    </h1>
  </div>
</body>
</html>
```